Web Design for Webdesign company 3 page PSD

Project
---------
We need a PSD Web Design to be used in a WordPress installation.
What we would like to create is a professional looking website for a web design agency. We also need you to look for suitable stock images to be placed on these pages.
We need the design for:
Homepage
Landing page
Contact page
attached in the pages file you will find a file with more in depth details how these files should be build up.
We would like to see a desktop version and a mobile version of these pages
The website should have a 1100px width.
The mobile design should have 480px width.
The homepage should have a header slider about 450px high.
The slider is preferred full width and should have some images text and a button
Objectives
-------------
The main objective for the website is to get leads from customers in the form of a request for a quotation or a call or mail me back action. The most important action for the homepage is to link and navigate to our landing pages.
What we want to tell our visitors (our main products)
-------------------------------------------------------------------
- A website with no big investment but a monthly rate
- A successful website with no worries (a complete website, seo, hosting and a service contract for future customization is included for a monthly rate)
Color Scheme
------------
Use branding colors. You can find them in the branding.pdf file.
Additional colors:
White: #ffffff
Black: #181818
Company info
--------------
We are a starting web design / marketing agency based in The Netherlands and looking for the design of our website. Our services are (custom) webdesign, website marketing or combinations of both. Our main customer group is small business owners.
We sell websites but give the option to buy it with a lease contract.
A second product is a default website with a complete service: SEO, hosting and a service contract for a monthly rate.
Content:
-----------
If not available place Lorem Ipsum text.
There will come about 400 words of text on the landing pages
Design Competition
--------------------------
Since this is a designing competition we would like to see your creativity.
What you can expect from us is a lot of feedback 7 days a week with short response time.
You can send us the first sketchy mock ups of the homepage and we will give feedback based on these design. But we like your feedback or comments as well
Read the pages file for more in depth details how the pages should be designed

Target Market(s)
Small business owners in The Netherlands
Industry/Entity Type
It Company
Number of Pages Required
3 page
Requirements
Must have
- Homepage:
- Header slider with images, some text and a link to a custom page
- The slider should have 3 designed slides
- Landings page:
- Sidebar
- Action button for a request for a quotation
- Action button for a call me back action
- Action button for an appointment
- Contact form:
- Address details
- Contact form
Nice to have
- Homepage:
- Full width slider
- Testimonial block
- Blog items
Should not have
- Flash
- A to crowded design

```html
<!DOCTYPE html>
<html lang="en">
<head>
<meta charset="utf-8">
<title>Oak Row Web Studio</title>
<link href="https://fonts.googleapis.com/css2?family=Oswald:wght@400;500&family=Roboto:wght@400;500&display=swap" rel="stylesheet">
<style>
:root{
  --brand:#3f8276;
  --form-green:#5b9273;
  --field-green:#447c5f;
  --footer-teal:#4e8783;
  --bar:#1b1b1b;
  --white:#ffffff;
  --ink:#181818;
  --blue:#2a8fd6;
  --blue-dark:#1c6fb0;
}
*{margin:0;padding:0;box-sizing:border-box}
html,body{width:1200px;height:996px;overflow:hidden}
body{position:relative;font-family:'Roboto',sans-serif;background:var(--white);color:var(--ink)}
.site-header{position:absolute;left:0;top:0;width:1200px;height:123px;background:var(--white);box-shadow:0 2px 6px rgba(0,0,0,.15);z-index:2}
.brand{position:absolute;left:89px;top:46px;display:flex;align-items:center;gap:10px;font-family:'Roboto',sans-serif;font-weight:500;font-size:20px;color:var(--brand)}
.brand-dot{width:28px;height:28px;border-radius:50%;background:var(--brand)}
.main-nav{position:absolute;right:90px;top:60px;display:flex;gap:35px;font-size:14px;letter-spacing:.2px}
.main-nav a{color:var(--ink);text-decoration:none}
.main-nav a.is-active{color:var(--brand)}
.hero{position:absolute;left:0;top:123px;width:1200px;height:578px;background:linear-gradient(180deg,#a9c4d2 0%,#6f98ad 35%,#4b7890 65%,#34586b 100%)}
.hero-photo{position:absolute;left:0;top:0;width:100%;height:100%}
.quote-box{position:absolute;left:89px;top:351px;width:286px;height:350px;background:var(--form-green)}
.quote-title{height:48px;background:var(--white);font-family:'Oswald',sans-serif;font-size:21px;color:var(--brand);text-align:center;line-height:48px;font-weight:400}
.quote-field{position:absolute;left:17px;width:251px;height:33px;background:var(--field-green);border:1px solid rgba(255,255,255,.25);border-radius:3px;color:var(--white);font-size:12.5px;padding-left:13px;line-height:31px}
.send-btn{position:absolute;left:52px;top:288px;width:170px;height:34px;border-radius:3px;background:linear-gradient(#f4f4f4,#cfd3d6);font-size:17px;color:var(--ink);text-align:center;line-height:34px;font-family:'Roboto',sans-serif}
.hero-copy{position:absolute;left:399px;top:348px;color:var(--white)}
.hero-title{font-family:'Oswald',sans-serif;font-weight:400;font-size:50px;line-height:60px;letter-spacing:-.5px}
.hero-price{font-family:'Oswald',sans-serif;font-weight:400;font-size:30px;line-height:38px;margin-top:-2px}
.hero-text{position:absolute;left:2px;top:108px;width:400px;font-size:15.5px;line-height:27px}
.btn-primary{position:absolute;left:405px;top:530px;width:198px;height:50px;background:linear-gradient(var(--blue),var(--blue-dark));border:1px solid #5bb0ea;border-radius:3px;color:var(--white);font-size:15.5px;text-align:center;line-height:48px}
.btn-ghost{position:absolute;left:618px;top:533px;width:141px;height:40px;border:1px solid var(--white);border-radius:20px;color:var(--white);font-size:14px;text-align:center;line-height:38px}
.site-footer{position:absolute;left:0;top:701px;width:1200px;height:191px;background:var(--footer-teal);color:var(--white)}
.footer-brand{position:absolute;left:99px;top:80px;font-size:15px;font-weight:500;width:140px}
.footer-about{position:absolute;left:261px;top:60px;width:228px;font-size:13px;line-height:23px}
.btn-appointment{position:absolute;left:263px;top:120px;width:175px;height:36px;border:1px solid var(--white);border-radius:18px;font-size:11.5px;text-align:center;line-height:34px;letter-spacing:.2px}
.footer-col{position:absolute;top:47px}
.footer-col h3{font-size:15px;font-weight:500;letter-spacing:.3px;margin-bottom:17px}
.footer-col li{list-style:none;font-size:13px;line-height:28.5px}
.bottom-bar{position:absolute;left:0;top:892px;width:1200px;height:104px;background:var(--bar);color:var(--white);font-size:13px}
.legal{position:absolute;left:89px;top:31px;line-height:24px}
.legal span.sep{margin:0 7px}
.social{position:absolute;left:971px;top:37px;display:flex;gap:12px}
.social span{width:29px;height:29px;display:block}
</style>
</head>
<body>
<header class="site-header">
  <div class="brand"><span class="brand-dot"></span>Oak Row Web Studio</div>
  <nav class="main-nav">
    <a class="is-active" href="#">HOME</a>
    <a href="#">ABOUT US</a>
    <a href="#">SERVICES</a>
    <a href="#">PROJECT</a>
    <a href="#">BLOG</a>
    <a href="#">CONTACTS</a>
  </nav>
</header>

<section class="hero">
  <div class="hero-photo" role="img" aria-label="Photo of a man working on a laptop while sitting on a rock above a misty mountain valley"></div>
</section>

<form class="quote-box" style="position:absolute">
  <h2 class="quote-title">REQUEST A QUOTATION</h2>
  <div class="quote-field" style="top:69px">Name</div>
  <div class="quote-field" style="top:120px">Email ID</div>
  <div class="quote-field" style="top:174px">Phone</div>
  <div class="quote-field" style="top:225px">Message</div>
  <div class="send-btn">Send</div>
</form>

<div class="hero-copy">
  <h1 class="hero-title">A WEBSITE FROM</h1>
  <p class="hero-price">€19,95 PER MONTH</p>
  <p class="hero-text">With us, you can lease a website. So no big investment upfront. A website is available from € 19.95 per month</p>
</div>
<a class="btn-primary">MORE INFORMATION</a>
<a class="btn-ghost">CALL ME BACK</a>

<footer class="site-footer">
  <div class="footer-brand">Oak Row Web Studio</div>
  <p class="footer-about">Lorem Ipsum is simply dummy text of the printing and typesetting industry</p>
  <div class="btn-appointment">MAKE AN APPOINTMENT</div>
  <div class="footer-col" style="left:553px">
    <h3>LINK</h3>
    <ul><li>About us</li><li>Services</li><li>Presentation</li></ul>
  </div>
  <div class="footer-col" style="left:703px">
    <h3>AGENCIES</h3>
    <ul><li>Sign Up</li><li>E-mail form</li><li>Location map</li></ul>
  </div>
  <div class="footer-col" style="left:865px">
    <h3>CONTACT US</h3>
    <ul><li>42 Linden Lane, Harbourton, HT2 7QL</li><li>Phone: +1 800 555 0142</li><li>E-mail: hello@oakrowweb.example</li></ul>
  </div>
</footer>

<div class="bottom-bar">
  <div class="legal">
    Privacy Policy<span class="sep">|</span>Terms of Use<span class="sep">|</span>About Us<span class="sep">|</span>Sitemap<br>
    Copyright © 2015 &nbsp;All Rights
  </div>
  <div class="social">
    <span style="background:#1da1e2"></span>
    <span style="background:#d7221f"></span>
    <span style="background:#35559a"></span>
    <span style="background:#0d73b0"></span>
  </div>
</div>
</body>
</html>
```